Realty Group Needs Classy, Contemporary Letterhead Design

We need a letterhead design for a new realty company located in NY, USA. We buy investment properties to rehabilitate and or keep in our rental portfolio.

```html
<!DOCTYPE html>
<html lang="en">
<head>
<meta charset="utf-8">
<title>Meridale Realty Group – Letterhead</title>
<link href="https://fonts.googleapis.com/css2?family=Inter:wght@400;600;700;800&family=Arimo:wght@400&display=swap" rel="stylesheet">
<style>
  :root {
    --backdrop: #ededed;
    --paper: #ffffff;
    --brand: #4b2a8c;
    --brand-ink: #2b1f4a;
    --body-ink: #4f4f4f;
    --muted: #6e6e6e;
    --signature-tint: #e6e3ee;
  }
  * { box-sizing: border-box; margin: 0; padding: 0; }
  html, body {
    width: 1039px; height: 1200px; overflow: hidden;
    background: var(--backdrop);
  }
  .letterhead {
    position: absolute; left: 93px; top: 0;
    width: 852px; height: 1200px;
    background: var(--paper);
    font-family: "Arimo", Arial, sans-serif;
    color: var(--body-ink);
  }
  .brand {
    position: absolute; left: 64px; top: 98px;
    display: flex; align-items: center; gap: 10px;
  }
  .brand-mark {
    width: 14px; height: 14px; background: var(--brand);
  }
  .brand-name {
    font-family: "Inter", Arial, sans-serif;
    font-weight: 800; font-size: 34px; letter-spacing: -0.5px;
    color: var(--brand); line-height: 1;
  }
  .contact {
    position: absolute; left: 575px; top: 64px;
    padding-left: 22px; border-left: 1px solid var(--brand);
    font-family: "Inter", Arial, sans-serif;
    font-size: 13px; line-height: 16px; color: var(--brand-ink);
    letter-spacing: 0.2px;
  }
  .contact-company { font-weight: 600; color: var(--brand); }
  .contact-lines { margin-top: 8px; list-style: none; }
  .contact-lines li { display: flex; align-items: center; gap: 5px; }
  .contact-lines svg { width: 10px; height: 10px; fill: var(--brand); flex: none; }
  .letter {
    position: absolute; left: 64px; top: 400px; width: 720px;
  }
  .salutation { font-size: 17px; margin-bottom: 22px; }
  .letter p.body {
    font-size: 13px; line-height: 20px; text-align: justify;
    hyphens: auto; margin-bottom: 20px;
  }
  .closing { font-size: 13px; line-height: 20px; margin-top: 0; }
  .signature {
    display: block; margin-top: 20px; width: 110px; height: 44px;
    background: var(--signature-tint); border-radius: 3px;
  }
  .web {
    position: absolute; left: 0; right: 0; top: 1136px;
    text-align: center;
    font-family: "Inter", Arial, sans-serif;
    font-size: 12px; letter-spacing: 2px; color: var(--brand);
  }
  .web strong { font-weight: 700; }
</style>
</head>
<body>
<main class="letterhead">
  <header>
    <div class="brand">
      <span class="brand-mark"></span>
      <span class="brand-name">MERIDALE</span>
    </div>
    <address class="contact" style="font-style:normal">
      <div class="contact-company">Meridale Realty Group, LLC</div>
      <div>1240 Linden Avenue</div>
      <div>Albany, New York 12203</div>
      <ul class="contact-lines">
        <li><svg viewBox="0 0 10 10"><path d="M2 0.5 L3.6 0.5 L4.2 2.8 L3 3.6 Q4 5.8 6.4 7 L7.2 5.8 L9.5 6.4 L9.5 8 Q9.5 9.5 8 9.5 Q0.5 9 0.5 2 Q0.5 0.5 2 0.5Z"/></svg>518-555-0142</li>
        <li><svg viewBox="0 0 10 10"><rect x="2.5" y="0.5" width="5" height="3"/><rect x="0.5" y="3.5" width="9" height="4" rx="1"/><rect x="2.5" y="6.5" width="5" height="3" fill="#fff" stroke="#4b2a8c" stroke-width="1"/></svg>518-555-0178</li>
        <li><svg viewBox="0 0 10 10"><rect x="0.5" y="1.5" width="9" height="7"/><path d="M0.5 1.5 L5 5.5 L9.5 1.5" fill="none" stroke="#fff" stroke-width="1"/></svg>info@meridale.com</li>
      </ul>
    </address>
  </header>

  <section class="letter">
    <p class="salutation">Dear Mr. Smith,</p>
    <p class="body">Lorem ipsum dolor sit amet, consectetur adipiscing elit. Donec orci purus, luctus vitae dignissim eu, iaculis sed purus. Vivamus faucibus, ipsum nec aliquet viverra, leo mauris condimentum ligula, sit amet sagittis enim ligula quis arcu. Nam egestas tortor id nisi porttitor mattis. In tortor ante, ultricies in suscipit a, tempus non massa. Vivamus et auctor mi. Fusce vel massa nulla. Phasellus nec eros mauris, et scelerisque orci.</p>
    <p class="body">Donec malesuada orci vitae nulla accumsan porta a id massa. Quisque accumsan iaculis magna sit amet fringilla. Maecenas consequat, magna eget tincidunt semper, odio nibh rutrum mi, id feugiat ante nisi eu risus. Vestibulum nunc orci, rhoncus a placerat in, ultricies in mi. Cras mattis varius eros, vel fringilla nisi suscipit eget. Quisque scelerisque sagittis nulla at porttitor.</p>
    <p class="body">Sed id augue vitae urna euismod commodo aliquet a quam. Pellentesque arcu velit, cursus et malesuada ut, consequat et diam. Nullam erat sem, rhoncus id ullamcorper vitae, rhoncus et arcu. In ultricies ultricies nulla, ut rutrum nisi iaculis at. Donec eu magna a metus ornare faucibus. Fusce aliquet faucibus ultricies. Morbi semper, est id tincidunt gravida, sem arcu adipiscing lacus, ac bibendum nulla leo eu purus. Quisque nec diam sed risus consectetur a ccumsan quis quis nibh. Vestibulum id purus lorem.</p>
    <p class="closing">Sincerely,</p>
    <span class="signature" role="img" aria-label="Handwritten signature of the sender"></span>
  </section>

  <footer class="web">www.<strong>meridale</strong>.com</footer>
</main>
</body>
</html>
```